Design and Renovation Company Luxury Business Card

I want to create a luxury business card for a Design and Renovation Firm . We will use our current logo. The company name is 528BUILDA. We do not want anything standard. We need a very unique concept.
Please see uploaded inspiration. I really like the textured paper option. I would like the card to be thick with debossing, and/or embossing options. The logo has orange in it but I would like to see the card with and without the orange. I think the orange may make the company feel less high-end. The goal is to elevate the logo not match its vibe per se of the logo. We want something very unique, not standard at all!
I would like a space for :
Logo,
Name,
Position,
Email,
Office number,
Website Address,
Business Address,
Thank you!
Have fun!
Target Market(s)
Home owners Age 35 +
Industry/Entity Type
Design and Renovation
Contact Information for Business Card
Logo, Name, Position, Email, Office number, Website Address, Business Address,.
Colors
Designer to choose colors to be used in the design.
Requirements
Must have
- A luxury designer feel. Must be black or dark grey but open to other luxury ideas.
Nice to have
- Gold, silver, black embossing or debossing. Textured paper design.
Should not have
- A cheap look and feel.

```html
<!DOCTYPE html>
<html lang="en">
<head>
<meta charset="utf-8">
<title>528BUILDA Business Card</title>
<link href="https://fonts.googleapis.com/css2?family=Arimo:wght@400;700&display=swap" rel="stylesheet">
<style>
  :root {
    --page-bg: #1c1c1e;
    --card-face: #333335;
    --card-back-dark: #0d0d0e;
    --card-back-light: #4a4a4c;
    --ink: #ffffff;
    --ink-soft: #e6e6e6;
    --rule: #bdbdbd;
  }
  * { margin: 0; padding: 0; box-sizing: border-box; }
  html, body {
    width: 1200px; height: 874px; overflow: hidden;
    background: var(--page-bg);
    font-family: "Arimo", Arial, sans-serif;
  }
  .canvas { position: relative; width: 1200px; height: 874px; }
  .card {
    position: absolute; left: 260px; width: 680px; height: 388px;
    border-radius: 26px; overflow: hidden;
  }
  .card-back { top: 34px; }
  .card-back .pattern-area {
    width: 100%; height: 100%;
    background: linear-gradient(100deg, var(--card-back-dark) 0%, #1e1e20 45%, var(--card-back-light) 100%);
  }
  .card-front { top: 452px; background: var(--card-face); color: var(--ink); }

  .brand {
    position: absolute; right: 48px; top: 100px; text-align: right;
  }
  .brand-name {
    font-size: 40px; font-weight: 400; letter-spacing: 1px; line-height: 1;
    color: var(--ink);
  }
  .brand-tagline {
    margin-top: 8px;
    font-size: 13px; letter-spacing: 0.4px; color: var(--ink-soft);
  }

  .person { position: absolute; left: 44px; top: 168px; }
  .person-name { font-size: 24px; font-weight: 700; letter-spacing: 0.5px; }
  .person-role { font-size: 14px; color: var(--ink-soft); margin-top: 2px; }

  .divider {
    position: absolute; left: 44px; right: 72px; top: 232px;
    height: 1px; background: var(--rule);
  }

  .contacts { position: absolute; left: 44px; top: 246px; list-style: none; }
  .contacts li {
    display: flex; align-items: center; gap: 10px;
    font-size: 15px; line-height: 22px; color: var(--ink-soft);
  }
  .contacts svg { width: 13px; height: 13px; fill: none; stroke: var(--ink); stroke-width: 1.6; }
  .contacts .icon-fill { fill: var(--ink); stroke: none; }

  .address {
    position: absolute; right: 72px; top: 300px; text-align: right;
    font-size: 15px; line-height: 22px; color: var(--ink-soft);
  }
</style>
</head>
<body>
<main class="canvas">
  <section class="card card-back">
    <div class="pattern-area" role="img" aria-label="Back of card: field of small embossed squares fading from black to grey"></div>
  </section>

  <section class="card card-front">
    <div class="brand">
      <div class="brand-name">528BUILDA</div>
      <div class="brand-tagline">Design and Renovation Firm</div>
    </div>

    <div class="person">
      <div class="person-name">DANIEL HARLOW</div>
      <div class="person-role">President</div>
    </div>

    <div class="divider"></div>

    <ul class="contacts">
      <li>
        <svg viewBox="0 0 16 16" aria-hidden="true"><path class="icon-fill" d="M3.5 1.5l2.5 0 1 3.5-1.6 1.2a8 8 0 0 0 4.4 4.4l1.2-1.6 3.5 1v2.5c0 .8-.7 1.5-1.5 1.5C6.6 14 2 9.4 2 3c0-.8.7-1.5 1.5-1.5z"/></svg>
        604-218-5730
      </li>
      <li>
        <svg viewBox="0 0 16 16" aria-hidden="true"><rect x="1.5" y="3.5" width="13" height="9"/><path d="M1.5 3.5l6.5 5.5 6.5-5.5"/></svg>
        info@528builda.com
      </li>
      <li>
        <svg viewBox="0 0 16 16" aria-hidden="true"><circle cx="8" cy="8" r="6.5"/><path d="M1.5 8h13M8 1.5c2.5 2.5 2.5 10.5 0 13M8 1.5c-2.5 2.5-2.5 10.5 0 13"/></svg>
        www.528builda.com
      </li>
    </ul>

    <div class="address">
      4125 Cedarbrook Row<br>
      Kelowna, Canada 20418
    </div>
  </section>
</main>
</body>
</html>
```